A start-up named "Corvane Therapeutics" - needs a new PowerPoint design

We need a new PowerPoint Design for an early-stage start-up named "Corvane Therapeutics" seeking to disrupt the current approach towards drug discovery within aging disorders.

We would like to build on Corvane's legacy, the founder of the modern science of genetics, by employing a multidisciplinary approach, experimenting, and providing elderly patients the attention they deserve.

We have selected the suffix "therapeutics" intentionally as it stands for (a medicine) the treatment of disease; the science of healing. Alzheimer’s treatment is a huge, urgent, unmet need:
- Shift from a disease-management system to a preventive medicine system
- Focus on increasing the health span, not only the life span

Target Market(s)

Pharma/ Biotech Executives Medical Institutions Healthcare professionals (MDs, nurses, payors, pharmacists, etc.) Patients

Industry/Entity Type

Healthcare

Other font styles liked:
• Celias

Colors
0054AA
0677BA
7BADD7
CADEEF
E8F1F8
E54698
E96AAD
F1A4CE
F9D9EA
FCEFF6
A7469A
B969AE
D3A5CF
EDDBEB
F8F0F9
6B429C
8869AF
B7A5CE
E3DAEB
F3F0F8

Requirements
Must have
• - differentiate from other companies named after Corvane - differentiate from other Pharma/ Biotech companies
Nice to have
• simplicity/ minimalist logo vivid colors gradient 3D Life-Sciences inspired Simple geometry Balance
Should not have
• mascot/ emblem watermark logo animated ink style nature-inspired inventive typography artistic chaos

```html
<!DOCTYPE html>
<html lang="en">
<head>
<meta charset="utf-8">
<title>Corvane Therapeutics – Slide Template, Part 3</title>
<link href="https://fonts.googleapis.com/css2?family=Outfit:wght@400;500;600;700&family=Arimo:wght@700&display=swap" rel="stylesheet">
<style>
  :root{
    --page:#f2f0f1;
    --dark:#2a2a2c;
    --ink:#222;
    --blue:#0054AA;
    --blue-mid:#0677BA;
    --cyan:#1ea3e0;
    --pink:#E54698;
    --magenta:#c8327a;
    --purple:#8b3aa8;
    --plum:#3b1a5c;
    --gold:#e8b03a;
    --map:#8a8a8c;
    --row:#f2f2f2;
  }
  *{box-sizing:border-box;margin:0;padding:0}
  html,body{width:1200px;height:1200px;overflow:hidden;background:var(--page);font-family:"Outfit",sans-serif}
  .sheet{position:relative;width:1200px;height:1200px}

  .slide{position:absolute;width:547px;height:307px;overflow:hidden}
  .slide--dark{background:var(--dark);color:#fff}
  .slide--light{background:#fff;color:var(--ink)}
  .slide--map{left:42px;top:42px}
  .slide--timeline{left:612px;top:42px}
  .slide--table{left:42px;top:375px}
  .slide--closing{left:612px;top:375px;width:547px;height:308px}

  .top-bar{position:absolute;left:0;top:0;width:100%;height:3px;background:linear-gradient(90deg,var(--magenta),var(--purple))}
  .slide-title{position:absolute;left:17px;top:19px;font-size:17.5px;font-weight:600;letter-spacing:.1px}
  .slide--dark .slide-title{color:var(--pink)}
  .slide--light .slide-title{color:var(--blue)}

  .footer-brand{position:absolute;left:17px;top:280px;display:flex;align-items:center;gap:4px}
  .footer-brand .mark{width:9px;height:9px;background:var(--blue-mid)}
  .footer-brand .name{font-size:10px;font-weight:500;color:var(--blue-mid)}
  .footer-band{position:absolute;right:0;bottom:0;width:140px;height:22px}
  .footer-band svg{position:absolute;inset:0}
  .footer-text{position:absolute;left:30px;top:7px;font-size:5.6px;color:#fff;white-space:nowrap}
  .footer-text b{font-weight:600;margin-left:3px;padding-left:3px;border-left:.6px solid #fff}

  /* map */
  .map-area{position:absolute;left:85px;top:63px;width:376px;height:196px;border-radius:40px 60px 30px 50px;background:linear-gradient(135deg,#7c7c7e,var(--map));opacity:.9}
  .pin{position:absolute;width:20px;height:20px;margin:-10px 0 0 -10px;border-radius:50%;background:radial-gradient(circle at 35% 30%,#2f6fc0,#1a2f6a);color:#fff;font-size:6.5px;font-weight:600;display:flex;align-items:center;justify-content:center;box-shadow:0 1px 3px rgba(0,0,0,.5)}
  .pin-label{position:absolute;white-space:nowrap}
  .pin-label h4{font-size:7px;font-weight:600;color:var(--pink)}
  .pin-label p{font-size:5.8px;color:#fff;margin-top:2px}
  .pin-label--right{text-align:right}

  /* timeline */
  .timeline-line{position:absolute;left:0;top:157px;width:100%;height:2px;background:var(--pink)}
  .node{position:absolute;top:158px;width:24px;height:24px;margin:-12px 0 0 -12px;border-radius:50%;display:flex;align-items:center;justify-content:center}
  .node i{width:13px;height:13px;border-radius:50%}
  .stem{position:absolute;width:0;border-left:1px dashed}
  .stem::after{content:"";position:absolute;left:-3px;width:5px;height:5px;border-radius:50%;background:currentColor}
  .stem--up::after{top:-2px}
  .stem--down::after{bottom:-2px}
  .year{position:absolute;font-size:10px;font-weight:600;transform:translateX(-50%)}
  .event{position:absolute;font-size:7.8px;line-height:9.5px;width:90px}

  /* table */
  .data-table{position:absolute;left:17px;top:61px;width:513px;border-collapse:collapse;font-size:10.5px}
  .data-table th,.data-table td{height:32px;text-align:left;padding-left:4.5px;font-weight:400}
  .data-table thead th{background:var(--plum);color:#fff;font-weight:600}
  .data-table tbody th{color:var(--blue);font-weight:600}
  .data-table tbody tr:nth-child(even){background:var(--row)}
  .data-table tbody tr:last-child{border-bottom:1.5px solid var(--plum)}
  .data-table col.first{width:68px}

  /* closing */
  .closing-brand{position:absolute;left:19px;top:33px;display:flex;align-items:center;gap:6px}
  .closing-brand .mark{width:26px;height:26px;background:var(--blue)}
  .closing-brand .name{font-size:15px;font-weight:500;line-height:16px;color:var(--blue)}
  .thanks{position:absolute;left:18px;top:103px;font-size:48px;font-weight:700;color:var(--blue);letter-spacing:.5px;white-space:nowrap}
  .closing-rule{position:absolute;left:19px;top:169px;width:254px;height:1px;background:#c9c9c9}
  .closing-note{position:absolute;left:19px;top:178px;font-size:9.5px;color:#333;white-space:nowrap}
  .photo{position:absolute;inset:0;clip-path:polygon(375px 0,547px 0,547px 308px,260px 308px);background:linear-gradient(170deg,#3f8de0 0%,#6f8ee0 35%,#b07ac8 60%,#d2508e 85%,#c8327a 100%)}
  .accents{position:absolute;inset:0}
  .part-label{position:absolute;left:45px;top:1053px;font-family:"Arimo",Arial,sans-serif;font-weight:700;font-size:113px;line-height:1;color:#111;letter-spacing:-1px}
</style>
</head>
<body>
<main class="sheet">

  <!-- Map slide -->
  <section class="slide slide--dark slide--map">
    <div class="top-bar"></div>
    <h2 class="slide-title">Map Slide</h2>
    <div class="map-area" role="img" aria-label="World map with office locations"></div>

    <div class="pin-label pin-label--right" style="right:424px;top:136px"><h4>Section Header</h4><p>Lorem ipsum dolor sit amet.</p></div>
    <div class="pin" style="left:143px;top:145px">01</div>
    <div class="pin-label" style="left:264px;top:85px"><h4>Section Header</h4><p>Lorem ipsum dolor sit amet.</p></div>
    <div class="pin" style="left:274px;top:119px">03</div>
    <div class="pin-label" style="left:412px;top:106px"><h4>Section Header</h4><p>Lorem ipsum dolor sit amet.</p></div>
    <div class="pin" style="left:392px;top:118px">02</div>
    <div class="pin-label" style="left:286px;top:163px"><h4>Section Header</h4><p>Lorem ipsum dolor sit amet.</p></div>
    <div class="pin" style="left:266px;top:175px">05</div>
    <div class="pin-label pin-label--right" style="right:372px;top:197px"><h4>Section Header</h4><p>Lorem ipsum dolor sit amet.</p></div>
    <div class="pin" style="left:198px;top:208px">06</div>
    <div class="pin-label" style="left:427px;top:217px"><h4>Section Header</h4><p>Lorem ipsum dolor sit amet.</p></div>
    <div class="pin" style="left:407px;top:229px">04</div>

    <div class="footer-brand"><span class="mark"></span><span class="name">Corvane</span></div>
    <div class="footer-band">
      <svg width="140" height="22" viewBox="0 0 140 22" aria-hidden="true">
        <defs><linearGradient id="band1" x1="0" x2="1"><stop offset="0" stop-color="#c8327a"/><stop offset="1" stop-color="#8b3aa8"/></linearGradient></defs>
        <polygon points="0,22 12,0 20,0 8,22" fill="#0054AA"/>
        <polygon points="8,22 20,0 140,0 140,22" fill="url(#band1)"/>
      </svg>
      <span class="footer-text">Copywrite Statement 2022<b>11</b></span>
    </div>
  </section>

  <!-- Timeline slide -->
  <section class="slide slide--dark slide--timeline">
    <div class="top-bar"></div>
    <h2 class="slide-title">Timeline</h2>
    <div class="timeline-line"></div>

    <div class="stem stem--up" style="left:43px;top:66px;height:90px;color:var(--blue-mid);border-color:var(--blue-mid)"></div>
    <div class="stem stem--down" style="left:170px;top:160px;height:87px;color:var(--gold);border-color:var(--gold)"></div>
    <div class="stem stem--up" style="left:297px;top:66px;height:90px;color:var(--pink);border-color:var(--pink)"></div>
    <div class="stem stem--down" style="left:424px;top:160px;height:87px;color:var(--cyan);border-color:var(--cyan)"></div>

    <div class="node" style="left:43px;background:rgba(6,119,186,.45)"><i style="background:var(--blue-mid)"></i></div>
    <div class="node" style="left:170px;background:rgba(232,176,58,.45)"><i style="background:var(--gold)"></i></div>
    <div class="node" style="left:297px;background:rgba(229,70,152,.45)"><i style="background:var(--pink)"></i></div>
    <div class="node" style="left:424px;background:rgba(30,163,224,.45)"><i style="background:var(--cyan)"></i></div>

    <span class="year" style="left:43px;top:174px;color:var(--blue-mid)">2014</span>
    <span class="year" style="left:170px;top:127px;color:var(--gold)">2014</span>
    <span class="year" style="left:297px;top:174px;color:var(--pink)">2014</span>
    <span class="year" style="left:424px;top:127px;color:var(--cyan)">2014</span>

    <p class="event" style="left:55px;top:62px">Lorem ipsum dolor sit amet, consecteturat es adipiscing elit.</p>
    <p class="event" style="left:309px;top:62px">Lorem ipsum dolor sit amet, consecteturat es adipiscing elit.</p>
    <p class="event" style="left:181px;top:220px">Lorem ipsum dolor sit amet, consecteturat es adipiscing elit.</p>
    <p class="event" style="left:435px;top:220px">Lorem ipsum dolor sit amet, consecteturat es adipiscing elit.</p>

    <div class="footer-brand"><span class="mark"></span><span class="name">Corvane</span></div>
    <div class="footer-band">
      <svg width="140" height="22" viewBox="0 0 140 22" aria-hidden="true">
        <defs><linearGradient id="band2" x1="0" x2="1"><stop offset="0" stop-color="#c8327a"/><stop offset="1" stop-color="#8b3aa8"/></linearGradient></defs>
        <polygon points="0,22 12,0 20,0 8,22" fill="#0054AA"/>
        <polygon points="8,22 20,0 140,0 140,22" fill="url(#band2)"/>
      </svg>
      <span class="footer-text">Copywrite Statement 2022<b>12</b></span>
    </div>
  </section>

  <!-- Table slide -->
  <section class="slide slide--light slide--table">
    <div class="top-bar"></div>
    <h2 class="slide-title">Table Slide</h2>
    <table class="data-table">
      <colgroup><col class="first"><col span="7"></colgroup>
      <thead><tr><th>Data</th><th>Header</th><th>Header</th><th>Header</th><th>Header</th><th>Header</th><th>Header</th><th>Header</th></tr></thead>
      <tbody>
        <tr><th>Value</th><td>00</td><td>00</td><td>00</td><td>00</td><td>00</td><td>00</td><td>00</td></tr>
        <tr><th>Value</th><td>00</td><td>00</td><td>00</td><td>00</td><td>00</td><td>00</td><td>00</td></tr>
        <tr><th>Value</th><td>00</td><td>00</td><td>00</td><td>00</td><td>00</td><td>00</td><td>00</td></tr>
        <tr><th>Value</th><td>00</td><td>00</td><td>00</td><td>00</td><td>00</td><td>00</td><td>00</td></tr>
        <tr><th>Value</th><td>00</td><td>00</td><td>00</td><td>00</td><td>00</td><td>00</td><td>00</td></tr>
      </tbody>
    </table>

    <div class="footer-brand"><span class="mark"></span><span class="name">Corvane</span></div>
    <div class="footer-band">
      <svg width="140" height="22" viewBox="0 0 140 22" aria-hidden="true">
        <defs><linearGradient id="band3" x1="0" x2="1"><stop offset="0" stop-color="#c8327a"/><stop offset="1" stop-color="#8b3aa8"/></linearGradient></defs>
        <polygon points="0,22 12,0 20,0 8,22" fill="#0054AA"/>
        <polygon points="8,22 20,0 140,0 140,22" fill="url(#band3)"/>
      </svg>
      <span class="footer-text">Copywrite Statement 2022<b>13</b></span>
    </div>
  </section>

  <!-- Closing slide -->
  <section class="slide slide--light slide--closing">
    <div class="photo" role="img" aria-label="Scientist in a lab coat examining a test tube in a laboratory"></div>
    <svg class="accents" width="547" height="308" viewBox="0 0 547 308" aria-hidden="true">
      <line x1="364" y1="0" x2="317" y2="109" stroke="#e8b03a" stroke-width="1.5"/>
      <polygon points="263,221 299,221 260,308 223,308" fill="#3fb0e6"/>
      <polygon points="285,221 299,221 260,308 246,308" fill="#1e8fd0"/>
    </svg>
    <div class="closing-brand"><span class="mark"></span><span class="name">Corvane<br>Therapeutics</span></div>
    <h1 class="thanks">Thank You!</h1>
    <div class="closing-rule"></div>
    <p class="closing-note">Lorem ipsum dolor sit amet, consectetur adipiscing elit.</p>
  </section>

  <div class="part-label">PART 3</div>
</main>
</body>
</html>
```